All-Natural Head Lice Removal company

I need a business card with my pre-existing logo. We are a new company located in Portland Oregon that goes into peoples homes to help with head lice removal. My products and approach are all- natural and also will be around children.On my current logo we used Teal Bl and the color Green. I am open to new ideas just want it simple and creative

Target Market(s)

my biggest market is families of school aged children

Industry/Entity Type

Business

Contact Information for Business Card

see upload for details from previous business card

Font styles to use
Serif

Colors
33a6d7
9bcb3b
f37122

Requirements
Must have
• Basic information/ logo put into a creative format that is catching to the eye
Nice to have
• creative

```html
<!DOCTYPE html>
<html lang="en">
<head>
<meta charset="UTF-8">
<title>Clear Crown Business Card</title>
<link href="https://fonts.googleapis.com/css2?family=Comic+Neue:wght@400;700&display=swap" rel="stylesheet">
<style>
  :root {
    --teal: #33a6d7;
    --green: #9bcb3b;
    --leaf: #5aa83a;
    --ink: #1a1a1a;
    --text: #333333;
    --paper: #ffffff;
    --stage: #e9e6e1;
    --photo-warm: #6b4a3c;
    --photo-cool: #3f5f7a;
  }
  * { box-sizing: border-box; margin: 0; padding: 0; }
  html, body { width: 1200px; height: 843px; overflow: hidden; }
  body {
    background: var(--stage);
    font-family: "Comic Neue", "Comic Sans MS", cursive;
    display: flex;
    align-items: center;
    justify-content: center;
    gap: 48px;
  }
  .card {
    position: relative;
    width: 540px;
    height: 309px;
    border-radius: 16px;
    overflow: hidden;
    background: var(--paper);
    box-shadow: 0 6px 18px rgba(0,0,0,0.18);
  }
  .card-shapes { position: absolute; inset: 0; width: 100%; height: 100%; }

  /* back */
  .card-photo {
    position: absolute; left: 0; top: 0; width: 100%; height: 248px;
    background: radial-gradient(ellipse at 45% 40%, #c98a7a 0%, var(--photo-warm) 45%, var(--photo-cool) 100%);
  }
  .card-band {
    position: absolute; left: 0; bottom: 0; width: 100%; height: 61px;
    background: var(--teal);
    color: var(--paper);
    font-size: 17px;
    line-height: 1.2;
    padding: 9px 20px;
  }
  .back-brand {
    position: absolute; right: 22px; bottom: 76px;
    display: flex; align-items: center; gap: 8px;
    font-weight: 700; font-size: 24px; color: var(--ink);
    background: var(--paper); padding: 4px 12px; border-radius: 18px;
  }
  .brand-dot { width: 22px; height: 22px; border-radius: 50%; background: var(--green); }

  /* front */
  .front-brand {
    position: absolute; right: 34px; top: 64px;
    display: flex; align-items: center; gap: 10px;
    font-weight: 700; font-size: 34px; color: var(--ink);
  }
  .front-brand .brand-dot { width: 40px; height: 40px; }
  .contact { position: absolute; left: 34px; top: 118px; }
  .contact-name { font-weight: 700; font-size: 24px; color: var(--teal); }
  .contact-role { font-size: 16px; color: var(--green); margin-bottom: 14px; }
  .contact-list { list-style: none; font-size: 17px; color: var(--text); }
  .contact-list li { display: flex; align-items: center; gap: 9px; line-height: 1.4; }
  .contact-list svg { width: 14px; height: 14px; fill: var(--teal); flex: none; }
</style>
</head>
<body>

  <section class="card card-back">
    <div class="card-photo" role="img" aria-label="Photo of a child having her hair combed through while reading a picture book"></div>
    <div class="back-brand"><span class="brand-dot"></span>Clear Crown</div>
    <div class="card-band">Try Clear Crown Today and See the Difference<br>All Natural In-Home Lice Removal</div>
  </section>

  <section class="card card-front">
    <svg class="card-shapes" viewBox="0 0 540 309" aria-hidden="true">
      <path d="M0,0 H300 Q110,18 0,100 Z" fill="var(--teal)"/>
      <path d="M0,100 Q110,18 300,0" fill="none" stroke="var(--ink)" stroke-width="5"/>
      <path d="M540,309 H250 Q450,290 540,195 Z" fill="var(--leaf)"/>
      <path d="M250,309 Q450,290 540,195" fill="none" stroke="var(--ink)" stroke-width="5"/>
    </svg>
    <div class="front-brand"><span class="brand-dot"></span>Clear Crown</div>
    <div class="contact">
      <p class="contact-name">Dana Whitfield</p>
      <p class="contact-role">Owner</p>
      <ul class="contact-list">
        <li><svg viewBox="0 0 16 16"><path d="M3 1h3l1.5 4-2 1.3a9 9 0 0 0 4.2 4.2L11 8.5l4 1.5v3a2 2 0 0 1-2 2A12 12 0 0 1 1 3a2 2 0 0 1 2-2z"/></svg>1-800-555-0142</li>
        <li><svg viewBox="0 0 16 16"><path d="M1 3h14v10H1z M1 3l7 6 7-6" /></svg>dana@clearcrown.com</li>
        <li><svg viewBox="0 0 16 16"><circle cx="8" cy="8" r="7"/></svg>www.clearcrown.com</li>
      </ul>
    </div>
  </section>

</body>
</html>
```